Brintel Works - Fast, Efficient and Gas Mainteance for Domestic, Commercial and Industrial clients

We are in the process of purchasing a new business and would like to get a new logo and business card.
Business is a gas maintenance business that also does new gas installations.
Has been established since 1988.
Services include:
Install all types of gas appliances & equipment inc. hot water units
Maintain / repair / replace all types of gas appliances & equipment

Target Market(s)

Domestic, Commercial and Industrial clients

Industry/Entity Type

Business

Contact Information for Business Card

admin@brintelworks.com.au
07 3918 4726
Brintel Works PTY LTD

Logo Text

Gas Fitting & Plumbing Maintenance Specialists

Font styles to use
Sans Serif

Requirements
Must have
• Logo
• Business name, contact number, email address, web address
• Domestic | Commercial | Industrial Est Since 1988
Nice to have
• Possibly a black card with a flame logo to one side
Should not have
• Spelling errors

```html
<!DOCTYPE html>
<html lang="en">
<head>
<meta charset="utf-8">
<title>Brintel Works – Business Card</title>
<link href="https://fonts.googleapis.com/css2?family=Arimo:wght@400;700&display=swap" rel="stylesheet">
<style>
  :root {
    --backdrop: #1d2127;
    --blue-deep: #0d4ea6;
    --blue-mid: #0a6cc4;
    --blue-glow: #00aeea;
    --white: #ffffff;
    --icon-blue: #1a80d4;
  }
  html, body {
    margin: 0;
    padding: 0;
    width: 1200px;
    height: 1200px;
    overflow: hidden;
    background: var(--backdrop);
    font-family: "Arimo", Arial, sans-serif;
  }
  .stage {
    position: relative;
    width: 1200px;
    height: 1200px;
  }
  .card {
    position: absolute;
    left: 214px;
    width: 803px;
    height: 446px;
    border-radius: 32px;
    overflow: hidden;
    color: var(--white);
  }
  .card-front {
    top: 130px;
    background: radial-gradient(ellipse 380px 300px at 48% 45%, var(--blue-glow) 0%, var(--blue-mid) 50%, var(--blue-deep) 100%);
  }
  .card-back {
    top: 638px;
    background: radial-gradient(ellipse 560px 380px at 71% 85%, var(--blue-glow) 0%, var(--blue-mid) 50%, var(--blue-deep) 100%);
  }
  .brand-name {
    font-weight: 700;
    letter-spacing: 2px;
    line-height: 1;
    margin: 0;
  }
  .card-front .brand-name {
    position: absolute;
    left: 0;
    right: 0;
    top: 170px;
    text-align: center;
    font-size: 100px;
  }
  .service-line {
    position: absolute;
    left: 0;
    right: 0;
    top: 296px;
    margin: 0;
    text-align: center;
    font-size: 17px;
    letter-spacing: 1.5px;
    word-spacing: 2px;
    text-transform: uppercase;
  }
  .card-back .brand-name {
    position: absolute;
    left: 64px;
    top: 296px;
    font-size: 58px;
    letter-spacing: 1px;
  }
  .company-legal {
    position: absolute;
    left: 67px;
    top: 365px;
    font-size: 19px;
    letter-spacing: 0.6px;
    word-spacing: 3px;
  }
  .contact-list {
    position: absolute;
    right: 77px;
    top: 0;
    margin: 0;
    padding: 0;
    list-style: none;
  }
  .contact-list li {
    position: absolute;
    right: 0;
    white-space: nowrap;
    font-size: 22px;
    line-height: 1;
    transform: translateY(-50%);
    letter-spacing: 0.3px;
  }
  .contact-list .address { top: 145px; word-spacing: 4px; }
  .contact-list .phone { top: 194px; word-spacing: 4px; }
  .contact-list .email { top: 243px; }
  .contact-list .web { top: 292px; }
  .icon-tab {
    position: absolute;
    left: 742px;
    top: 76px;
    width: 61px;
    height: 291px;
    background: var(--white);
    border-radius: 18px 0 0 18px;
  }
  .icon-tab .divider {
    position: absolute;
    left: 0;
    width: 42px;
    height: 1.5px;
    background: var(--icon-blue);
  }
  .icon-tab .icon {
    position: absolute;
    left: 4px;
    width: 22px;
    height: 22px;
    transform: translateY(-50%);
  }
</style>
</head>
<body>
<main class="stage">
  <section class="card card-front" aria-label="Card front">
    <h1 class="brand-name">BRINTEL</h1>
    <p class="service-line">Domestic | Commercial | Industrial &nbsp;Est Since 1988</p>
  </section>

  <section class="card card-back" aria-label="Card back">
    <ul class="contact-list">
      <li class="address">Address 01, Address, City.</li>
      <li class="phone">07 3918 4726</li>
      <li class="email">admin@brintelworks.com.au</li>
      <li class="web">www.brintelworks.com.au</li>
    </ul>

    <div class="icon-tab">
      <svg class="icon" style="top:69px" viewBox="0 0 24 24" aria-hidden="true">
        <path d="M12 3 L2 12 H5 V21 H10 V15 H14 V21 H19 V12 H22 Z" fill="var(--icon-blue)"/>
      </svg>
      <span class="divider" style="top:90px"></span>
      <svg class="icon" style="top:118px" viewBox="0 0 24 24" aria-hidden="true">
        <path d="M6.5 2.5 L9.5 2 L11 7 L8.8 8.6 C9.6 11.6 11.8 14.6 14.6 16 L16.4 14 L21 16.2 L20.4 19.4 C19.8 21.2 17.6 21.8 15.6 21 C9.6 18.6 5 13 3.6 7.4 C3.2 5 4.4 3 6.5 2.5 Z" fill="var(--icon-blue)"/>
      </svg>
      <span class="divider" style="top:140px"></span>
      <svg class="icon" style="top:167px" viewBox="0 0 24 24" aria-hidden="true">
        <circle cx="12" cy="12" r="4" fill="none" stroke="var(--icon-blue)" stroke-width="2.6"/>
        <path d="M16 8 V14 C16 16.5 20.5 16.5 20.5 12 A8.5 8.5 0 1 0 16 19.5" fill="none" stroke="var(--icon-blue)" stroke-width="2.6" stroke-linecap="round"/>
      </svg>
      <span class="divider" style="top:192px"></span>
      <svg class="icon" style="top:216px" viewBox="0 0 24 24" aria-hidden="true">
        <g fill="none" stroke="var(--icon-blue)" stroke-width="1.8">
          <circle cx="12" cy="12" r="9.5"/>
          <ellipse cx="12" cy="12" rx="4.2" ry="9.5"/>
          <line x1="2.5" y1="12" x2="21.5" y2="12"/>
          <line x1="12" y1="2.5" x2="12" y2="21.5"/>
          <path d="M4.2 7 H19.8 M4.2 17 H19.8"/>
        </g>
      </svg>
      <span class="divider" style="top:242px"></span>
    </div>

    <p class="brand-name">BRINTEL</p>
    <span class="company-legal">Brintel Works PTY LTD</span>
  </section>
</main>
</body>
</html>
```